I need a logo design for a new company based in Tucson called "Mindtrail Lee Corwin". I am a psychotherapist that specializes in clinical psychology with athletes and performers. The final design should incorporate the psychology symbol as a watermark. The logo should convey movement and fluidity. "Mindtrail" is a bit of a play on words combining psychology (head) with sports (coach). Other design interests include mid-century, Harold Ames Whitby. I will want to use the logo for business cards, letterhead and marketing brochures. I will put together a website at a later date. I am attaching a file with some pertinent information for the business card. Thank you.
Lee Corwin
mindtrailleecorwin@quillpost.net

Thank you all for the submissions so far.  I have submitted an additional file with a draft of a new design idea.  Since "mindtrail" is a bit of a play on words, I would like to see something with the two "H's" look something like quotation marks.  If the psychology logo is to be included at all, it needs to be less prominent.     Thank you all.  Lee                               

Target Market(s)

1) Adolescent and adult athletes and performers who are looking to increase their level of performance (Sport and Performance Psychology)
2) Adult psychotherapy patients (Clinical psychology)

Industry/Entity Type

Marketing

Colors

Designer to choose colors to be used in the design.

Requirements
Must have
• 1) Since "mindtrail" is a bit of a play on words, The "H's" need to be in a font that looks somewhat like quotation marks.

Nice to have
• Logo on one side. All other info on the backside?

```html
<!DOCTYPE html>
<html lang="en">
<head>
<meta charset="utf-8">
<title>Mindtrail – Business Card</title>
<link rel="stylesheet" href="https://fonts.googleapis.com/css2?family=Alegreya:wght@500&family=Lato:wght@400;700&display=swap">
<style>
  :root {
    --backdrop: #a3a3a3;
    --card: #3c3a3b;
    --card-edge: #2a2829;
    --ink: #d2d2d2;
    --ink-soft: #b9b9b9;
  }
  * { box-sizing: border-box; margin: 0; padding: 0; }
  html, body {
    width: 1200px; height: 1000px; overflow: hidden;
    background: var(--backdrop);
  }
  .stage { position: relative; width: 1200px; height: 1000px; }
  .card {
    position: absolute;
    width: 640px; height: 390px;
    background: var(--card);
    border-radius: 22px;
    box-shadow: 0 6px 0 var(--card-edge);
    color: var(--ink);
    overflow: hidden;
  }
  .card--front { left: 500px; top: 70px; }
  .card--back { left: 60px; top: 500px; }

  .brand {
    position: absolute; left: 50%; top: 50%;
    transform: translate(-50%, -50%);
    text-align: center; white-space: nowrap;
  }
  .brand__row { display: flex; align-items: center; justify-content: center; gap: 16px; }
  .brand__mark { width: 22px; height: 22px; background: var(--ink); }
  .brand__name {
    font-family: "Lato", sans-serif; font-weight: 700;
    font-size: 64px; letter-spacing: 6px; color: var(--ink);
    text-transform: uppercase;
  }
  .brand__tagline {
    margin-top: 10px;
    font-family: "Lato", sans-serif; font-weight: 700;
    font-size: 19px; letter-spacing: 3px; color: var(--ink-soft);
    text-transform: uppercase;
  }

  .holder { position: absolute; left: 70px; top: 58px; white-space: nowrap; }
  .holder__name {
    font-family: "Alegreya", serif; font-weight: 500;
    font-size: 46px; color: var(--ink); line-height: 1;
  }
  .holder__title {
    margin: 8px 0 0 140px;
    font-family: "Lato", sans-serif; font-size: 18px; color: var(--ink-soft);
  }
  .contact {
    position: absolute; left: 0; right: 0; top: 200px;
    text-align: center; list-style: none; white-space: nowrap;
    font-family: "Lato", sans-serif; font-size: 20px; line-height: 1.55;
    color: var(--ink);
  }
  .contact__label { font-weight: 700; }
</style>
</head>
<body>
<main class="stage">
  <section class="card card--front" aria-label="Card front">
    <div class="brand">
      <div class="brand__row">
        <span class="brand__mark" aria-hidden="true"></span>
        <span class="brand__name">Mindtrail</span>
      </div>
      <p class="brand__tagline">Clinical &amp; Performance Psychology</p>
    </div>
  </section>

  <section class="card card--back" aria-label="Card back">
    <div class="holder">
      <h1 class="holder__name">Leland H. Corwin, MA, LLC</h1>
      <p class="holder__title">Licensed Professional Counselor</p>
    </div>
    <ul class="contact">
      <li><span class="contact__label">Fax:</span> 555.201.0142</li>
      <li><span class="contact__label">Mobile:</span> 555.201.0187</li>
      <li><span class="contact__label">Email:</span> mindtrailleecorwin@quillpost.net</li>
      <li><span class="contact__label">Address:</span> 4120 East Sabino Way #210 Larkmoor, NV 89921</li>
    </ul>
  </section>
</main>
</body>
</html>
```